Need App for Impact Related Events

My app is to help with internal events. When you enter the prompted event code the next screen shows you everyone currently at the event. It will give you the ability to Start a conversation with someone you met at that event, or signal it is your turn to send a message. The next screen is a message thread with that person. I am looking for a design that incorporates the colors and ‘feel good’ emotion of our logo. I have pieced together a pretty good interpretation of what I’m looking for in the attached mockup by slicing and dicing designs. I also attached our logo mascot.Screens (see attached mockups)

Note 1: I do not like the picture on the screen used in screen one because it makes it seem like a dating app. I attached an alternative photo that can be used or present different ideas.

Note 2: On the login/signup screen (screen 2) I need an additional first and last name for login, you can try to fit this on one login screen or present a two step signup screen where that is presented in the second screen.

READ MOCKUP GUIDELINES UNDER Must Haves

Target Market(s)

People attending internal social impact events

Industry/Entity Type

Charity

Font styles to use
Sans Serif

Colors
86cfc6

Requirements
Must have
• Follow the screen mockups attached to project
• PLEASE READ
• I have provided a relatively close design of what I’m looking for in the mockups. Some screens need to be followed more closely to my design mockup than other. I have listed a guide below how how closely you should follow my mockup design exactly. Overall I would like to see some ideas of incorporating a few accent colors so it doesn’t appear SO Blue. I also attached some app inspiration designs I found from around the web
• Screen Mockup Guideline Follow %
• Screen 1: 65% - mostly on target, would like to see ways to make it not SO Blue and possibly creative places to add some explainer text describing the app
• Screen 2: 50% - general design idea is here, but more open
• Screen 3: 35% - a lot more room for design influence
• Screen 4: 70% - mostly on target, a little room for design influence/color scheme ideas
• Screen 5-6: 25% - a lot of room for design change/ideas/influence
• Screen 7-8: 80% - already very close to what I need, maybe open to slight sizing and color scheme ideas
• Screen 9: 15% - the most open for influence, only the general functionality of the screen is communicated here
Nice to have
• Please Read Mockup Guideline above. In large part I am looking for something to use some nice accent colors so it is not overwhelmingly blue and bring the whole design into a seamless style.
Should not have

```html
<!DOCTYPE html>
<html lang="en">
<head>
<meta charset="utf-8">
<title>Event People</title>
<link href="https://fonts.googleapis.com/css2?family=Nunito+Sans:wght@400;600;700;800&display=swap" rel="stylesheet">
<style>
:root{
  --teal:#1ec8c4;
  --teal-soft:#86cfc6;
  --coral:#ff7a66;
  --coral-deep:#f2604c;
  --sun:#ffc857;
  --plum:#7a6cc8;
  --ink:#2b2f33;
  --muted:#7d8286;
  --line:#e6e8ea;
  --white:#ffffff;
  --avatar-a:#b08474;
  --avatar-b:#6b5346;
  --avatar-c:#9a86c4;
}
*{box-sizing:border-box;margin:0;padding:0}
html,body{width:675px;height:1200px;overflow:hidden;background:var(--white)}
body{font-family:"Nunito Sans",sans-serif;color:var(--ink);position:relative}
.event-header{position:absolute;left:0;top:0;width:675px;height:424px;overflow:hidden}
.event-header__backdrop{position:absolute;inset:0;background:linear-gradient(135deg,#5fdcd6 0%,var(--teal) 45%,#17a9a6 78%,#3f9fb8 100%)}
.event-header__accent{position:absolute;left:0;bottom:0;width:675px;height:8px;background:linear-gradient(90deg,var(--coral) 0%,var(--sun) 50%,var(--plum) 100%)}
.back-button{position:absolute;left:36px;top:50px}
.host-avatar{position:absolute;left:579px;top:34px;width:64px;height:64px;border-radius:50%;background:var(--avatar-b);border:3px solid var(--sun)}
.event-title{position:absolute;left:58px;top:156px;font-size:56px;font-weight:800;color:var(--white);letter-spacing:.3px;line-height:1}
.event-group{position:absolute;left:58px;top:238px;font-size:28px;font-weight:700;color:var(--sun)}
.event-meta{position:absolute;left:58px;top:279px;list-style:none;color:var(--white);font-size:26px;font-weight:600}
.event-meta li{display:flex;align-items:center;height:46px}
.event-meta svg{width:26px;height:26px;margin-right:26px;flex:none}
.more-menu{position:absolute;left:634px;top:370px}
.section-title{position:absolute;left:30px;top:448px;font-size:36px;font-weight:600}
.section-title::after{content:"";position:absolute;left:2px;bottom:-8px;width:44px;height:4px;border-radius:2px;background:var(--coral)}
.divider{position:absolute;left:0;width:675px;height:2px;background:var(--line)}
.person{position:absolute;left:0;width:675px}
.person__avatar{position:absolute;left:39px;top:0;width:64px;height:64px;border-radius:50%}
.person__avatar--a{background:var(--avatar-a);box-shadow:0 0 0 3px var(--white),0 0 0 6px var(--sun)}
.person__avatar--b{background:var(--avatar-b)}
.person__avatar--c{background:var(--avatar-c)}
.person__name{position:absolute;left:133px;font-size:30px;font-weight:600;white-space:nowrap}
.person__preview{position:absolute;left:133px;top:33px;font-size:24px;color:var(--muted);white-space:nowrap}
.person__time{position:absolute;right:30px;top:-8px;font-size:21px;color:var(--muted)}
.person__time--new{color:var(--coral-deep);font-weight:700}
.say-hi{position:absolute;left:488px;top:561px;width:159px;height:75px;border:none;border-radius:8px;background:var(--coral);color:var(--white);font-family:inherit;font-size:26px;font-weight:800;letter-spacing:1px}
.tab-indicator{position:absolute;left:60px;top:1098px;width:17px;height:17px;border-radius:50%;background:var(--coral)}
.tab-icon{position:absolute}
.add-button{position:absolute;left:286px;top:1084px;width:104px;height:104px;border-radius:50%;background:linear-gradient(135deg,var(--coral) 0%,var(--coral-deep) 100%);display:flex;align-items:center;justify-content:center}
</style>
</head>
<body>
<header class="event-header">
  <div class="event-header__backdrop" role="img" aria-label="Party table scene with gift ribbons, cups and confetti in teal tones"></div>
  <div class="event-header__accent"></div>
  <svg class="back-button" width="28" height="36" viewBox="0 0 28 36"><path d="M20 4 L6 18 L20 32" fill="none" stroke="#fff" stroke-width="4" stroke-linecap="round" stroke-linejoin="round"/></svg>
  <div class="host-avatar" role="img" aria-label="Host profile photo"></div>
  <h1 class="event-title">Nadia's Birthday</h1>
  <p class="event-group">Family</p>
  <ul class="event-meta">
    <li><svg viewBox="0 0 24 24"><path d="M12 2a7 7 0 0 0-7 7c0 5 7 13 7 13s7-8 7-13a7 7 0 0 0-7-7zm0 9.5A2.5 2.5 0 1 1 12 6.5a2.5 2.5 0 0 1 0 5z" fill="#fff"/></svg>C-12, Lane 4, Harbor Row</li>
    <li><svg viewBox="0 0 24 24" fill="none" stroke="#fff" stroke-width="2"><rect x="3" y="3" width="7" height="7"/><rect x="14" y="3" width="7" height="7"/><rect x="3" y="14" width="7" height="7"/><path d="M14 14h3v3h-3zM18 18h3v3h-3z"/></svg>ACRT54W</li>
    <li><svg viewBox="0 0 24 24" fill="none" stroke="#fff" stroke-width="2"><rect x="3" y="5" width="18" height="16" rx="2"/><path d="M3 10h18M8 3v4M16 3v4"/></svg>22 - Sep - 2018</li>
  </ul>
  <svg class="more-menu" width="14" height="40" viewBox="0 0 14 40"><circle cx="7" cy="6" r="4" fill="#fff"/><circle cx="7" cy="20" r="4" fill="#fff"/><circle cx="7" cy="34" r="4" fill="#fff"/></svg>
</header>

<h2 class="section-title">People</h2>
<div class="divider" style="top:515px"></div>

<section class="person" style="top:566px">
  <div class="person__avatar person__avatar--a" role="img" aria-label="Profile photo"></div>
  <p class="person__name" style="top:12px">Maya Collins</p>
</section>
<button class="say-hi">SAY HI!</button>
<div class="divider" style="top:674px"></div>

<section class="person" style="top:729px">
  <div class="person__avatar person__avatar--b" role="img" aria-label="Profile photo"></div>
  <p class="person__name" style="top:-9px">Rohan Ellis</p>
  <p class="person__preview">You: Nice to meet you!</p>
  <p class="person__time person__time--new">12:49</p>
</section>
<div class="divider" style="top:834px"></div>

<section class="person" style="top:889px">
  <div class="person__avatar person__avatar--c" role="img" aria-label="Profile photo"></div>
  <p class="person__name" style="top:-9px">Clara Quinn</p>
  <p class="person__preview">Great, we'll discuss this idea further.</p>
  <p class="person__time">03:51</p>
</section>
<div class="divider" style="top:996px"></div>

<nav aria-label="Main navigation">
  <span class="tab-indicator"></span>
  <svg class="tab-icon" style="left:44px;top:1128px" width="48" height="48" viewBox="0 0 24 24" fill="none" stroke="var(--teal)" stroke-width="2"><rect x="3" y="4" width="18" height="17" rx="2"/><path d="M3 9h18M8 2v4M16 2v4"/></svg>
  <svg class="tab-icon" style="left:183px;top:1132px" width="42" height="42" viewBox="0 0 24 24" fill="none" stroke="var(--teal)" stroke-width="2.2"><path d="M12 3a9 9 0 1 0 4.5 16.8L21 21l-1.3-4.3A9 9 0 0 0 12 3z" stroke-linejoin="round"/></svg>
  <div class="add-button"><svg width="44" height="44" viewBox="0 0 24 24"><path d="M12 4v16M4 12h16" stroke="#fff" stroke-width="2.4" stroke-linecap="round"/></svg></div>
  <svg class="tab-icon" style="left:452px;top:1130px" width="42" height="46" viewBox="0 0 24 26" fill="none" stroke="var(--teal)" stroke-width="2.2" stroke-linejoin="round"><path d="M5 18V11a7 7 0 0 1 14 0v7l2 2H3z"/><path d="M10 23h4" stroke-linecap="round"/></svg>
  <svg class="tab-icon" style="left:585px;top:1132px" width="46" height="42" viewBox="0 0 24 22" fill="none" stroke="var(--teal)" stroke-width="2.2" stroke-linecap="round"><path d="M2 6h20M2 16h20"/><circle cx="15" cy="6" r="3" fill="#fff"/><circle cx="8" cy="16" r="3" fill="#fff"/></svg>
</nav>
</body>
</html>
```